Tradeshwo display 8x10 high resolution backdrop

I created a backdrop I wanted to use via Chat GPT but the image isn't high quality enough for print so I want someone to recreate it as close as possible to my creation. See attached, TY!

```html
<!DOCTYPE html>
<html lang="en">
<head>
<meta charset="utf-8">
<title>Keystone Flow Systems – Trade Show Backdrop</title>
<link rel="stylesheet" href="https://fonts.googleapis.com/css2?family=Barlow:wght@600;700;800&family=Barlow+Semi+Condensed:wght@500;600;700&display=swap">
<style>
  :root{
    --stage:#c9cbcb;
    --paper:#ffffff;
    --ink:#262626;
    --navy:#07183d;
    --navy-2:#0a2559;
    --royal:#0b47b8;
    --royal-2:#1763d6;
    --bright:#2a8cf0;
    --sky:#9cc8ef;
    --text-dark:#1c1c1c;
  }
  *{box-sizing:border-box;margin:0;padding:0}
  html,body{width:1200px;height:814px;overflow:hidden;background:var(--stage)}
  .backdrop{position:absolute;left:0;top:31px;width:1200px;height:751px;background:var(--paper);overflow:hidden;font-family:"Barlow Semi Condensed",sans-serif;color:var(--text-dark)}
  .layer{position:absolute;left:0;top:0;width:1200px;height:751px}
  .abs{position:absolute}

  /* brand */
  .brand{left:50px;top:52px;display:flex;align-items:center;gap:14px}
  .brand-dot{width:22px;height:22px;border-radius:50%;background:var(--royal)}
  .brand-name{font-family:"Barlow",sans-serif;font-weight:800;font-size:34px;line-height:1.02;color:var(--navy);text-transform:uppercase;letter-spacing:.5px}

  /* value icons */
  .values{left:384px;top:78px;display:flex;height:92px}
  .value{width:84px;display:flex;flex-direction:column;align-items:center;border-left:1.5px solid #b8c2d4}
  .value svg{width:42px;height:42px}
  .value-label{margin-top:10px;font-family:"Barlow",sans-serif;font-weight:600;font-size:11.5px;line-height:13px;text-align:center;color:var(--navy-2)}

  /* headline */
  .headline-top{left:56px;top:188px;font-family:"Barlow",sans-serif;font-weight:800;font-size:58px;line-height:1;color:var(--ink);letter-spacing:.2px}
  .headline-main{left:54px;top:240px;font-family:"Barlow",sans-serif;font-weight:800;font-size:71px;line-height:1;letter-spacing:1.6px;
    background:linear-gradient(180deg,#1b6fe0 0%,#0a45b0 55%,#062f8a 100%);-webkit-background-clip:text;background-clip:text;color:transparent}
  .tagline{left:58px;top:319px;width:720px;display:flex;align-items:center;gap:18px}
  .tagline-rule{flex:1;height:2px;background:var(--navy-2)}
  .tagline-text{font-family:"Barlow",sans-serif;font-weight:700;font-size:17px;letter-spacing:3.4px;color:var(--navy-2);white-space:nowrap}

  .banner-text{left:64px;top:359px;font-family:"Barlow",sans-serif;font-weight:700;font-size:16.5px;letter-spacing:3.3px;color:#fff}

  /* products */
  .product{top:402px;display:flex;flex-direction:column;align-items:center;text-align:center}
  .product-image{width:118px;height:132px;border-radius:14px}
  .product-title{margin-top:6px;font-weight:700;font-size:13.5px;color:var(--royal);letter-spacing:.1px;white-space:nowrap}
  .product-desc{margin-top:3px;font-weight:600;font-size:11.4px;line-height:18.8px;color:var(--text-dark);white-space:nowrap}
  .divider{top:404px;width:1px;height:208px;background:#d3d8e0}

  /* feature panels */
  .feature{left:1000px;font-family:"Barlow",sans-serif;font-weight:700;font-size:16.5px;line-height:19.5px;color:#fff;text-transform:uppercase}

  /* footer */
  .servicing{left:105px;top:684px;font-family:"Barlow",sans-serif;font-weight:600;color:#fff}
  .servicing .label{font-size:13.5px;letter-spacing:.3px}
  .servicing .states{font-size:13px;margin-top:6px;letter-spacing:.2px}
  .footer-rule{top:683px;width:1.5px;height:42px;background:#fff;opacity:.85}
  .website{left:482px;top:694px;font-family:"Barlow",sans-serif;font-weight:700;font-size:25px;color:#fff;letter-spacing:.3px}
  .website .accent{color:var(--bright)}
  .partner{left:848px;top:685px;font-family:"Barlow",sans-serif}
  .partner .lead{font-weight:600;font-size:13.5px;color:#fff}
  .partner .claim{font-weight:800;font-size:22px;color:var(--bright);margin-top:2px;letter-spacing:.2px}
</style>
</head>
<body>
<div class="backdrop">

  <svg class="layer" viewBox="0 0 1200 751" aria-hidden="true">
    <defs>
      <linearGradient id="photoTone" x1="0" y1="0" x2="0" y2="1">
        <stop offset="0" stop-color="#6f96c2"/>
        <stop offset=".35" stop-color="#d9c59a"/>
        <stop offset=".55" stop-color="#2c4a6e"/>
        <stop offset="1" stop-color="#1e4f8f"/>
      </linearGradient>
      <linearGradient id="swoosh" x1="0" y1="0" x2="1" y2="1">
        <stop offset="0" stop-color="#d6e8f8"/>
        <stop offset=".5" stop-color="#5f9fe0"/>
        <stop offset="1" stop-color="#1b4fa6"/>
      </linearGradient>
      <linearGradient id="bannerTone" x1="0" y1="0" x2="1" y2="0">
        <stop offset="0" stop-color="#0a2d7a"/>
        <stop offset=".6" stop-color="#0d46b5"/>
        <stop offset="1" stop-color="#1660d6"/>
      </linearGradient>
      <linearGradient id="footerTone" x1="0" y1="0" x2="0" y2="1">
        <stop offset="0" stop-color="#0a2a66"/>
        <stop offset=".3" stop-color="#07183d"/>
        <stop offset="1" stop-color="#061434"/>
      </linearGradient>
      <linearGradient id="panelTone" x1="0" y1="0" x2="1" y2="0">
        <stop offset="0" stop-color="#07183d"/>
        <stop offset="1" stop-color="#0a2559"/>
      </linearGradient>
    </defs>

    <!-- curved accent bands -->
    <path d="M680 0 L760 0 C 800 120, 860 250, 905 360 L880 360 C 830 240, 760 110, 680 0Z" fill="#e6f1fb"/>
    <path d="M700 0 L745 0 C 790 120, 850 250, 900 360 L888 360 C 838 240, 770 115, 700 0Z" fill="url(#swoosh)"/>

    <!-- photo area -->
    <path d="M745 0 L1200 0 L1200 360 L900 360 C 850 250, 795 120, 745 0Z" fill="url(#photoTone)" role="img" aria-label="Photo of a water treatment plant with circular clarifier tanks at sunrise"/>

    <!-- banner -->
    <path d="M0 350 L774 350 L790 369 L774 388 L0 388Z" fill="url(#bannerTone)"/>

    <!-- feature panels -->
    <g fill="url(#panelTone)" stroke="#2a8cf0" stroke-width="2">
      <path d="M912 246 L1202 246 L1202 331 L912 331 L894 288.5Z"/>
      <path d="M912 335 L1202 335 L1202 414 L912 414 L894 374.5Z"/>
      <path d="M912 418 L1202 418 L1202 496 L912 496 L894 457Z"/>
      <path d="M912 500 L1202 500 L1202 612 L912 612 L894 556Z"/>
    </g>

    <!-- footer wave -->
    <path d="M0 626 C 250 634, 480 672, 700 674 C 900 676, 1060 646, 1200 604 L1200 751 L0 751Z" fill="#3f7fd0" opacity=".55"/>
    <path d="M0 634 C 260 646, 480 680, 700 682 C 900 684, 1060 658, 1200 618 L1200 751 L0 751Z" fill="url(#footerTone)"/>

    <!-- feature icons -->
    <g fill="none" stroke="#fff" stroke-width="2.2" stroke-linecap="round" stroke-linejoin="round">
      <circle cx="958" cy="290" r="28"/>
      <path d="M958 274 C 952 284, 947 290, 947 297 A11 11 0 0 0 969 297 C 969 290, 964 284, 958 274Z"/>
      <path d="M953 299 A5 5 0 0 0 959 304"/>
      <path d="M958 346 L978 353 L978 370 C 978 384, 969 392, 958 397 C 947 392, 938 384, 938 370 L938 353Z"/>
      <path d="M949 372 L956 379 L968 364" stroke-width="3"/>
      <path d="M936 460 A22 22 0 0 1 980 460"/>
      <rect x="931" y="458" width="7" height="16" rx="3"/>
      <rect x="978" y="458" width="7" height="16" rx="3"/>
      <path d="M980 474 C 980 484, 971 487, 963 487"/>
      <circle cx="960" cy="487" r="2.5" fill="#fff"/>
      <path d="M946 470 C 951 476, 965 476, 970 470"/>
      <circle cx="958" cy="556" r="29"/>
      <path d="M946 568 L946 558 M954 568 L954 552 M962 568 L962 546" stroke-width="4"/>
      <path d="M944 548 L956 540 L962 544 L972 534 M966 534 L972 534 L972 540"/>
    </g>

    <!-- location pin -->
    <circle cx="72" cy="703" r="22" fill="#0d46b5" stroke="#fff" stroke-width="2"/>
    <path d="M72 716 C 66 708, 63 703, 63 698 A9 9 0 0 1 81 698 C 81 703, 78 708, 72 716Z" fill="#fff"/>
    <circle cx="72" cy="698" r="3.5" fill="#0d46b5"/>
  </svg>

  <!-- brand -->
  <div class="abs brand">
    <span class="brand-dot"></span>
    <span class="brand-name">Keystone Flow<br>Systems</span>
  </div>

  <!-- value icons -->
  <div class="abs values">
    <div class="value">
      <svg viewBox="0 0 42 42" fill="none" stroke="#0b47b8" stroke-width="1.8" stroke-linecap="round" stroke-linejoin="round" aria-hidden="true">
        <circle cx="21" cy="17" r="12"/><circle cx="21" cy="17" r="8"/>
        <path d="M17 17 L20 20 L25 14"/><path d="M14 27 L10 38 L15 35 L18 39 L21 29 L24 39 L27 35 L32 38 L28 27"/>
      </svg>
      <div class="value-label">QUALITY<br>BRANDS</div>
    </div>
    <div class="value">
      <svg viewBox="0 0 42 42" fill="none" stroke="#0b47b8" stroke-width="1.8" aria-hidden="true">
        <circle cx="21" cy="21" r="13" stroke-width="6" stroke-dasharray="5 5.2"/>
        <circle cx="21" cy="21" r="12"/><circle cx="21" cy="21" r="6"/>
      </svg>
      <div class="value-label">ENGINEERED<br>SOLUTIONS</div>
    </div>
    <div class="value">
      <svg viewBox="0 0 42 42" fill="none" stroke="#0b47b8" stroke-width="1.8" stroke-linecap="round" aria-hidden="true">
        <path d="M7 22 A14 14 0 0 1 35 22"/><rect x="4" y="21" width="6" height="11" rx="3"/><rect x="32" y="21" width="6" height="11" rx="3"/>
        <path d="M35 32 C 35 37, 29 38, 24 38"/><circle cx="21" cy="38" r="2.5"/>
      </svg>
      <div class="value-label">EXPERT<br>SUPPORT</div>
    </div>
    <div class="value">
      <svg viewBox="0 0 42 42" fill="none" stroke="#0b47b8" stroke-width="1.8" stroke-linecap="round" stroke-linejoin="round" aria-hidden="true">
        <path d="M2 14 L9 11 L15 26 L8 29Z"/><path d="M40 14 L33 11 L27 26 L34 29Z"/>
        <path d="M12 15 L19 13 L24 15 L17 20 C 19 22, 22 21, 25 19 L31 25"/>
        <path d="M30 15 L24 15"/><path d="M14 26 L19 31 M17 24 L22 29 M20 22 L25 27"/>
      </svg>
      <div class="value-label">TURNKEY<br>DELIVERY</div>
    </div>
  </div>

  <!-- headline -->
  <div class="abs headline-top">SOLUTIONS THAT</div>
  <div class="abs headline-main">KEEP WATER MOVING</div>
  <div class="abs tagline">
    <span class="tagline-rule"></span>
    <span class="tagline-text">EXPERTISE.&nbsp; RELIABILITY.&nbsp;&nbsp; RESULTS.</span>
    <span class="tagline-rule"></span>
  </div>
  <div class="abs banner-text">COMPLETE SOLUTIONS FOR THE WATER &amp; WASTEWATER INDUSTRY</div>

  <!-- products -->
  <div class="abs product" style="left:14px;width:160px">
    <div class="product-image" role="img" aria-label="Blue split-case centrifugal pump" style="background:radial-gradient(circle at 50% 50%,#2a5fcf 0%,#1c3f9a 55%,#ffffff 72%)"></div>
    <div class="product-title">PUMPS</div>
    <div class="product-desc">Industry leading pumps<br>built for performance,<br>efficiency &amp; reliability.</div>
  </div>
  <div class="abs divider" style="left:171px"></div>

  <div class="abs product" style="left:171px;width:146px">
    <div class="product-image" role="img" aria-label="Blue high efficiency electric motor" style="background:radial-gradient(circle at 50% 50%,#2c55c4 0%,#1a3791 55%,#ffffff 72%)"></div>
    <div class="product-title">MOTORS</div>
    <div class="product-desc">High efficiency motors<br>engineered for durability<br>and long life.</div>
  </div>
  <div class="abs divider" style="left:317px"></div>

  <div class="abs product" style="left:317px;width:170px">
    <div class="product-image" role="img" aria-label="Silver positive displacement blower" style="width:140px;background:radial-gradient(circle at 50% 50%,#9da3aa 0%,#6c7279 55%,#ffffff 72%)"></div>
    <div class="product-title">BLOWERS</div>
    <div class="product-desc">Aeron PD positive displacement<br>blowers for reliable, energy<br>efficient performance.</div>
  </div>
  <div class="abs divider" style="left:487px"></div>

  <div class="abs product" style="left:487px;width:136px">
    <div class="product-image" role="img" aria-label="Variable frequency drive cabinet with keypad" style="width:80px;border-radius:4px;background:linear-gradient(90deg,#3a3f47 0%,#2b3038 55%,#1d3a78 100%)"></div>
    <div class="product-title">VFD &amp; CONTROLS</div>
    <div class="product-desc">Precision control and<br>energy savings through<br>advanced VFD solutions.</div>
  </div>
  <div class="abs divider" style="left:623px"></div>

  <div class="abs product" style="left:623px;width:142px">
    <div class="product-image" role="img" aria-label="Blue control valve with grey actuator" style="width:90px;background:linear-gradient(180deg,#9aa0a8 0%,#6f767e 38%,#2450b8 60%,#1a3a8a 100%)"></div>
    <div class="product-title">AUTOMATION &amp; VALVES</div>
    <div class="product-desc">Smart automation and<br>reliable valves for optimized<br>system performance.</div>
  </div>
  <div class="abs divider" style="left:765px"></div>

  <div class="abs product" style="left:766px;width:120px">
    <svg class="product-image" viewBox="0 0 118 132" fill="none" aria-hidden="true">
      <circle cx="60" cy="46" r="21" stroke="#0b47b8" stroke-width="9" stroke-dasharray="7 6.2"/>
      <circle cx="60" cy="46" r="19" fill="#0b47b8"/>
      <circle cx="60" cy="46" r="12" fill="#fff"/>
      <path d="M60 37 C 56 43, 54 46, 54 49 A6 6 0 0 0 66 49 C 66 46, 64 43, 60 37Z" fill="#0b47b8"/>
      <path d="M28 82 C 40 76, 50 86, 64 84 C 74 82, 84 74, 92 70 C 98 68, 100 74, 96 78 C 86 88, 74 96, 58 96 C 46 96, 38 92, 32 92Z" fill="#0b47b8"/>
    </svg>
    <div class="product-title" style="font-size:13px">TURNKEY SOLUTIONS</div>
    <div class="product-desc">Complete systems<br>designed, integrated<br>and supported by KFS.</div>
  </div>

  <!-- feature text -->
  <div class="abs feature" style="top:260px">WATER &amp;<br>WASTEWATER<br>EXPERTISE</div>
  <div class="abs feature" style="top:355px">TRUSTED<br>PRODUCTS</div>
  <div class="abs feature" style="top:437px">LOCAL SUPPORT<br>YOU CAN COUNT ON</div>
  <div class="abs feature" style="top:508px">BUILT FOR<br>PERFORMANCE.<br>FOCUSED ON<br>YOUR SUCCESS.</div>

  <!-- footer -->
  <div class="abs servicing">
    <div class="label">SERVICING</div>
    <div class="states">VIRGINIA | NORTH CAROLINA | MARYLAND | DELAWARE</div>
  </div>
  <div class="abs footer-rule" style="left:456px"></div>
  <div class="abs website">www.<span class="accent">keystoneflow-va</span>.com</div>
  <div class="abs footer-rule" style="left:808px"></div>
  <div class="abs partner">
    <div class="lead">YOUR PARTNER FOR</div>
    <div class="claim">A BETTER FLOW FORWARD</div>
  </div>
</div>
</body>
</html>
```